Hollow Thicket, a 3d voxel survival video game needs a card for gaming conventions

I am the lead developer for Hollow Thicket http://www.HollowThicket.example and need a business card to hand out at an indie gaming convention
The card would need to include the game name, website url, my name, position (Lead Developer), e-mail and phone number
The game is a 3d, voxel (with smooth terrain) based survival game with guns and wildlife. The main icon of the game would likely be a grizzly bear but I am willing to accept other designs too.
Attached is a media kit for the game with some images you can use but don't have to its just what little art I can provide. Anything on the website or from the video game can also be used. unrelated art can also be used.
Target Market(s)
Indie Developers/publishers at conferences
Industry/Entity Type
Games
Contact Information for Business Card
Name: Corin Waldrick
Position: Lead Developer
E-mail: Pale_Kettle@mailbox.example
Phone number: 555-372-1186

```html
<!DOCTYPE html>
<html lang="en">
<head>
<meta charset="utf-8">
<title>Hollow Thicket — Business Card</title>
<link href="https://fonts.googleapis.com/css2?family=Rajdhani:wght@600;700&family=Roboto:wght@400&display=swap" rel="stylesheet">
<style>
  :root {
    --page-bg: #a9a7a8;
    --front-edge: #3f3d22;
    --front-mid: #8c8868;
    --front-glow: #e3ddc4;
    --back-edge: #b9b7a8;
    --back-glow: #f1efe9;
    --brand-red: #9e2a20;
    --band-red: #a51d1a;
    --band-olive: #98947a;
    --ink-dark: #1f1f1f;
    --ink-body: #2a2a2a;
    --fur-dark: #4e2e17;
    --fur-light: #9a6a42;
  }
  * { margin: 0; padding: 0; box-sizing: border-box; }
  html, body { width: 1200px; height: 1200px; overflow: hidden; }
  body { background: var(--page-bg); position: relative; font-family: "Roboto", Arial, sans-serif; }

  .card { position: absolute; width: 714px; height: 421px; overflow: hidden; }

  /* Front */
  .card-front {
    left: 237px; top: 118px;
    background: radial-gradient(ellipse 55% 60% at 50% 45%, var(--front-glow) 0%, var(--front-mid) 55%, var(--front-edge) 100%);
  }
  .front-mascot {
    position: absolute; left: 234px; top: 48px; width: 158px; height: 132px;
    border-radius: 50% 50% 30% 30%;
    background: radial-gradient(ellipse 60% 70% at 55% 35%, var(--fur-light), var(--fur-dark) 65%, rgba(78,46,23,0) 100%);
  }
  .front-brand {
    position: absolute; left: 0; right: 0; top: 196px;
    text-align: center;
    font-family: "Rajdhani", Arial, sans-serif; font-weight: 700;
    font-size: 62px; line-height: 58px; letter-spacing: 4px;
    text-transform: uppercase; color: var(--brand-red);
  }

  /* Back */
  .card-back {
    left: 229px; top: 643px; height: 422px;
    background: radial-gradient(ellipse 70% 80% at 55% 30%, var(--back-glow) 0%, var(--back-edge) 100%);
  }
  .back-mascot {
    position: absolute; left: 8px; top: 40px; width: 310px; height: 345px;
    border-radius: 45% 55% 20% 20%;
    background: radial-gradient(ellipse at 50% 40%, var(--fur-light), var(--fur-dark) 80%);
  }
  .back-brand {
    position: absolute; right: 46px; top: 36px; text-align: right;
    font-family: "Rajdhani", Arial, sans-serif; font-weight: 700;
    font-size: 56px; line-height: 56px; letter-spacing: 3px;
    text-transform: uppercase; color: var(--brand-red);
  }
  .person-name {
    position: absolute; right: 43px; top: 190px;
    font-family: "Rajdhani", Arial, sans-serif; font-weight: 700;
    font-size: 29px; color: var(--ink-dark);
  }
  .person-role {
    position: absolute; right: 43px; top: 228px;
    font-size: 16px; color: var(--ink-body);
  }
  .contact-list { position: absolute; right: 42px; top: 276px; list-style: none; }
  .contact-item {
    display: flex; justify-content: flex-end; align-items: center; gap: 16px;
    font-size: 17px; color: var(--ink-body); height: 25.5px;
  }
  .contact-item svg { width: 18px; height: 18px; fill: var(--ink-body); }
  .band-red { position: absolute; left: 0; bottom: 0; width: 390px; height: 20px; background: var(--band-red); }
  .band-olive { position: absolute; right: 0; bottom: 0; width: 340px; height: 42px; background: var(--band-olive);
    clip-path: polygon(22px 0, 100% 0, 100% 100%, 0 100%); }
</style>
</head>
<body>
  <section class="card card-front">
    <div class="front-mascot" role="img" aria-label="Photo of a roaring grizzly bear fading into the background"></div>
    <div class="front-brand">Hollow<br>Thicket</div>
  </section>

  <section class="card card-back">
    <div class="back-mascot" role="img" aria-label="Photo of a standing brown grizzly bear on a rock"></div>
    <div class="back-brand">Hollow<br>Thicket</div>
    <div class="person-name">Corin Waldrick</div>
    <div class="person-role">Lead Developer</div>
    <ul class="contact-list">
      <li class="contact-item">555-372-1186
        <svg viewBox="0 0 24 24" aria-hidden="true"><path d="M3 9c0-3 4-5 9-5s9 2 9 5v2h-5V8.5c-1-.6-2.4-.9-4-.9s-3 .3-4 .9V11H3z"/><path d="M6 12h12l2 8H4z"/><circle cx="12" cy="16" r="2" fill="#e8e6df"/></svg>
      </li>
      <li class="contact-item">www.hollowthicket.example
        <svg viewBox="0 0 24 24" aria-hidden="true"><path d="M12 2a10 10 0 1 0 0 20 10 10 0 0 0 0-20zm6.9 6h-3a15 15 0 0 0-1.3-3.9A8 8 0 0 1 18.9 8zM12 4c.8 1.1 1.5 2.5 1.9 4h-3.8c.4-1.5 1.1-2.9 1.9-4zM4.3 14a8 8 0 0 1 0-4h3.4a16 16 0 0 0 0 4zm.8 2h3a15 15 0 0 0 1.3 3.9A8 8 0 0 1 5.1 16zm3-8h-3a8 8 0 0 1 4.3-3.9C8.8 5.3 8.4 6.6 8.1 8zM12 20c-.8-1.1-1.5-2.5-1.9-4h3.8c-.4 1.5-1.1 2.9-1.9 4zm2.3-6H9.7a14 14 0 0 1 0-4h4.6a14 14 0 0 1 0 4zm.3 5.9c.6-1.2 1-2.5 1.3-3.9h3a8 8 0 0 1-4.3 3.9zM16.3 14a16 16 0 0 0 0-4h3.4a8 8 0 0 1 0 4z"/></svg>
      </li>
      <li class="contact-item">Pale_Kettle@mailbox.example
        <svg viewBox="0 0 24 24" aria-hidden="true"><path d="M2 5h20v14H2z M4 7v.5l8 6 8-6V7z" fill-rule="evenodd"/></svg>
      </li>
    </ul>
    <div class="band-olive"></div>
    <div class="band-red"></div>
  </section>
</body>
</html>
```